Vale Crest - Business Cards

We are a consultancy to help builders to optimize their planning in order to save building costs. For that reason we need a clean and professional business card for our high-priced services. A QR code should lead to the contact information needed.

```html
<!DOCTYPE html>
<html lang="en">
<head>
<meta charset="utf-8">
<title>Vale Crest - Business Cards</title>
<link rel="stylesheet" href="https://fonts.googleapis.com/css2?family=Roboto:wght@400;500&display=swap">
<style>
  :root {
    --backdrop: #2b2b2b;
    --card-dark: #1f1f20;
    --card-dark-2: #262627;
    --gold: #d9b15a;
    --gold-light: #e6c46a;
    --gold-deep: #b07f33;
    --text-light: #e9e9e9;
    --text-muted: #9a9a9a;
  }
  * { margin: 0; padding: 0; box-sizing: border-box; }
  html, body { width: 1200px; height: 1138px; overflow: hidden; }
  body {
    background: var(--backdrop);
    font-family: "Roboto", sans-serif;
    position: relative;
  }
  .card {
    position: absolute;
    border-radius: 16px;
    overflow: hidden;
    box-shadow: 0 6px 14px rgba(0,0,0,0.45);
  }
  .card-front {
    left: 274px; top: 186px; width: 624px; height: 376px;
    background: linear-gradient(135deg, var(--card-dark) 0%, var(--card-dark-2) 100%);
  }
  .front-name {
    position: absolute; left: 309px; top: 0;
    left: 35px; top: 118px;
    font-size: 30px; font-weight: 500; letter-spacing: 2px;
    color: var(--gold);
    text-transform: uppercase;
  }
  .front-web {
    position: absolute; left: 35px; top: 324px;
    font-size: 17px; color: var(--text-muted);
  }
  .card-back {
    left: 276px; top: 608px; width: 618px; height: 374px;
    background: var(--card-dark-2);
  }
  .back-shape { position: absolute; left: 0; top: 0; }
  .back-name-mark {
    position: absolute; left: 0; width: 328px; top: 212px;
    text-align: center;
    font-size: 30px; font-weight: 500; letter-spacing: 2px;
    color: #2a2a2a; text-transform: uppercase;
  }
  .contact-block {
    position: absolute; right: 39px; top: 86px;
    text-align: right; color: var(--text-light);
  }
  .contact-name { font-size: 23px; font-weight: 500; color: var(--gold); line-height: 28px; }
  .contact-role { font-size: 16px; line-height: 22px; }
  .contact-address { margin-top: 30px; font-size: 16px; line-height: 24px; }
  .contact-lines { margin-top: 6px; list-style: none; }
  .contact-lines li {
    font-size: 16px; line-height: 24px;
    display: flex; justify-content: flex-end; align-items: center; gap: 14px;
  }
  .contact-lines svg { width: 15px; height: 15px; fill: var(--gold); }
</style>
</head>
<body>
  <section class="card card-front">
    <div class="front-name">Vale Crest</div>
    <div class="front-web">www.valecrest.com</div>
  </section>

  <section class="card card-back">
    <svg class="back-shape" width="618" height="374" viewBox="0 0 618 374">
      <defs>
        <linearGradient id="goldFill" x1="0" y1="0" x2="0" y2="1">
          <stop offset="0" stop-color="#ad7a30"/>
          <stop offset="0.45" stop-color="#e2c062"/>
          <stop offset="0.7" stop-color="#d5ad55"/>
          <stop offset="1" stop-color="#a97730"/>
        </linearGradient>
      </defs>
      <path d="M0 0 H282 Q360 187 282 374 H0 Z" fill="#3a3a3e"/>
      <path d="M0 0 H266 Q350 187 266 374 H0 Z" fill="url(#goldFill)"/>
    </svg>
    <div class="back-name-mark">Vale Crest</div>

    <div class="contact-block">
      <div class="contact-name">Vale Crest</div>
      <div class="contact-role">Managing Director</div>
      <div class="contact-address">234 Anywhere St., Any City,<br>Any Town, US 123456</div>
      <ul class="contact-lines">
        <li>828-111-1111
          <svg viewBox="0 0 16 16"><path d="M2 5c0-2 2-3 6-3s6 1 6 3v1h-3V5H5v1H2z M4 7h8l2 7H2z"/></svg>
        </li>
        <li>john@yourwebsite.com
          <svg viewBox="0 0 16 16"><path d="M1 3h14v10H1z M2 4l6 5 6-5" stroke="#262627" stroke-width="1"/></svg>
        </li>
        <li>www.yourwebsite.com
          <svg viewBox="0 0 16 16"><circle cx="8" cy="8" r="7"/><path d="M1 8h14 M8 1v14 M8 1c-4 4-4 10 0 14 M8 1c4 4 4 10 0 14" stroke="#262627" stroke-width="1" fill="none"/></svg>
        </li>
      </ul>
    </div>
  </section>
</body>
</html>
```